Brightline Energy Product Distribution Brochure

We are looking to have our current brochure for our customers completely redesigned...the idea is to present the relevant information in an attractive way . Our website is brightlineenergyco.example where you can find more information about us. We have included a file with a rough idea of the page order and what each should include but feel free to adapt based on design. The example provided is only for context and doesnt have to be maintained. We will be using the brochure both digitally and in print form. As long as it reads easily and is eye catching, the design can be horizontal or vertical.Final deliverable should be indesign file.

"Our Brands" page: should be limited to one page (space being enough) where it has the header for each one (for example diesel generators) space for one or two lines of text and then the corresponding logos for each of the five categories
Updates

For those asking: the "our brands" page should be a single page layout where there is a header with the corresponding section and space for maybe one line of text followed by the two logos for that category. Each of the product pages should be similar in fashion to the one in the document attached: a photo of the product with some white space and space for the text to be included. We will be posting additional examples today

Target Market(s)

We want to present it to customers both digitally and in print so they can see our products

Industry/Entity Type

Power Generation

Font styles to use
Serif

Requirements
Must have
• Eye catching and able to present the information in a presentable fashion. Rest is up to you.
Nice to have
• Should incorporate the colors of our logo but can also add other depending on design

```html
<!DOCTYPE html>
<html lang="en">
<head>
<meta charset="utf-8">
<title>Brightline Energy – Our Distributors</title>
<link rel="stylesheet" href="https://fonts.googleapis.com/css2?family=Michroma&family=Montserrat:wght@400;600;700;800&display=swap">
<style>
  :root {
    --backdrop: #e6e5e1;
    --paper: #fbfbfc;
    --brand-blue: #3d3aa6;
    --brand-blue-light: #5a56c4;
    --circle-blue: #4f4bb8;
    --accent-yellow: #f3e600;
    --ink-soft: #c9c8ef;
    --photo-light: #e8e7ea;
    --photo-mid: #b9b8bc;
    --photo-dark: #6f6e72;
  }
  * { box-sizing: border-box; margin: 0; padding: 0; }
  html, body { width: 1200px; height: 960px; overflow: hidden; }
  body {
    background: var(--backdrop);
    font-family: "Montserrat", Arial, sans-serif;
    position: relative;
  }
  .spread {
    position: absolute;
    left: 40px; top: 190px;
    width: 1120px; height: 580px;
    display: flex;
    box-shadow: 0 10px 30px rgba(0,0,0,.15);
  }
  .page { position: relative; width: 560px; height: 580px; background: var(--paper); overflow: hidden; }

  /* Left page */
  .distributors-panel {
    position: absolute; left: 34px; top: 44px;
    width: 490px; height: 492px;
    background: linear-gradient(135deg, var(--brand-blue) 0%, var(--brand-blue-light) 100%);
    padding: 44px 36px 0 40px;
  }
  .section-title {
    font-family: "Michroma", "Arial Black", sans-serif;
    font-size: 25px; letter-spacing: 1px;
    color: var(--accent-yellow);
    font-weight: 400;
  }
  .section-intro {
    margin-top: 12px; width: 410px;
    font-size: 8.5px; line-height: 1.45;
    color: var(--ink-soft);
  }
  .benefit-grid { position: absolute; left: 0; top: 150px; width: 100%; height: 300px; }
  .benefit {
    position: absolute; width: 100px; text-align: center;
  }
  .benefit-icon {
    width: 96px; height: 86px; margin: 0 auto;
    border: 2px solid var(--accent-yellow); border-radius: 9px;
    display: flex; align-items: center; justify-content: center;
  }
  .benefit-icon svg { width: 46px; height: 46px; }
  .benefit-label {
    margin-top: 8px; font-size: 9px; font-weight: 700; color: #fff;
  }

  /* Right page */
  .photo-backdrop {
    position: absolute; inset: 0;
    background: radial-gradient(ellipse at 45% 55%, var(--photo-mid) 0%, var(--photo-light) 70%),
                var(--photo-light);
  }
  .photo-backdrop::after {
    content: ""; position: absolute; left: 170px; top: 30px; width: 210px; height: 470px;
    border-radius: 30px; background: linear-gradient(180deg, var(--photo-dark), #4f4e52);
    opacity: .35;
  }
  .signup-heading {
    position: absolute; left: 100px; top: 210px;
    width: 400px; height: 52px;
    border: 1.5px solid var(--accent-yellow);
    display: flex; align-items: center; justify-content: center;
    font-family: "Michroma", "Arial Black", sans-serif;
    font-size: 21px; color: var(--accent-yellow);
    transform: rotate(-3deg);
  }
  .step {
    position: absolute; top: 330px;
    width: 112px; height: 112px; border-radius: 50%;
    background: var(--circle-blue);
    display: flex; align-items: center; justify-content: center;
    text-align: center;
  }
  .step-number {
    position: absolute; inset: 0;
    display: flex; align-items: center; justify-content: center;
    font-size: 80px; font-weight: 800; color: rgba(255,255,255,.25);
  }
  .step-text {
    position: relative; font-size: 8px; font-weight: 700;
    color: var(--accent-yellow); line-height: 1.2; padding: 0 10px;
  }
  .step-1 { left: 40px; }
  .step-2 { left: 220px; top: 318px; }
  .step-3 { left: 400px; top: 310px; }
  .step-arrow { position: absolute; }
</style>
</head>
<body>
  <div class="spread">
    <section class="page page-left">
      <div class="distributors-panel">
        <h1 class="section-title">OUR DISTRIBUTORS</h1>
        <p class="section-intro">Our distributors gain access to protected territories, hands-on training, tiered discounts and flexible payment terms. Refer new partners and earn rewards while growing a reliable power business in your region with full support from us.</p>

        <div class="benefit-grid">
          <div class="benefit" style="left:40px; top:0;">
            <div class="benefit-icon">
              <svg viewBox="0 0 48 48"><rect x="10" y="6" width="3" height="38" fill="#fff"/><circle cx="11.5" cy="6" r="3" fill="#fff"/><path d="M14 10 Q22 6 28 10 T40 10 V26 Q34 30 28 26 T14 26 Z" fill="#fff"/></svg>
            </div>
            <div class="benefit-label">Territory</div>
          </div>
          <div class="benefit" style="left:195px; top:0;">
            <div class="benefit-icon">
              <svg viewBox="0 0 48 48"><circle cx="16" cy="12" r="7" fill="#fff"/><path d="M10 20 L20 40 L38 40 Q44 32 36 24 Q30 20 26 26 L20 20 Z" fill="#fff"/></svg>
            </div>
            <div class="benefit-label">Training</div>
          </div>
          <div class="benefit" style="left:350px; top:0;">
            <div class="benefit-icon">
              <svg viewBox="0 0 48 48"><circle cx="14" cy="14" r="6" fill="none" stroke="#fff" stroke-width="4"/><circle cx="34" cy="34" r="6" fill="none" stroke="#fff" stroke-width="4"/><line x1="38" y1="8" x2="10" y2="40" stroke="#fff" stroke-width="4" stroke-linecap="round"/></svg>
            </div>
            <div class="benefit-label">Discounts</div>
          </div>
          <div class="benefit" style="left:118px; top:128px;">
            <div class="benefit-icon">
              <svg viewBox="0 0 48 48"><circle cx="15" cy="18" r="5" fill="#fff"/><path d="M6 32 Q15 22 24 32 Z" fill="#fff"/><circle cx="33" cy="18" r="5" fill="#fff"/><path d="M24 32 Q33 22 42 32 Z" fill="#fff"/><path d="M16 8 Q24 2 32 8" fill="none" stroke="#fff" stroke-width="2.5"/><path d="M16 40 Q24 46 32 40" fill="none" stroke="#fff" stroke-width="2.5"/></svg>
            </div>
            <div class="benefit-label">Referral Program</div>
          </div>
          <div class="benefit" style="left:290px; top:128px;">
            <div class="benefit-icon">
              <svg viewBox="0 0 48 48"><path d="M10 4 H38 V42 L33 38 L28 42 L24 38 L20 42 L15 38 L10 42 Z" fill="none" stroke="#fff" stroke-width="2.5"/><g stroke="#fff" stroke-width="2.5"><line x1="16" y1="12" x2="32" y2="12"/><line x1="16" y1="18" x2="32" y2="18"/><line x1="16" y1="24" x2="32" y2="24"/><line x1="16" y1="30" x2="28" y2="30"/></g></svg>
            </div>
            <div class="benefit-label">Payment terms</div>
          </div>
        </div>
      </div>
    </section>

    <section class="page page-right">
      <div class="photo-backdrop" role="img" aria-label="Black and white photo of a hand holding a smartphone with a blank white screen"></div>

      <div class="signup-heading">Sign up process:</div>

      <div class="step step-1">
        <span class="step-number">1</span>
        <span class="step-text">Apply online<br>(brightlineenergyco.example)</span>
      </div>
      <svg class="step-arrow" style="left:158px; top:375px;" width="56" height="12" viewBox="0 0 56 12"><line x1="0" y1="7" x2="50" y2="5" stroke="#f3e600" stroke-width="1.5"/><path d="M46 1 L54 5 L46 9" fill="none" stroke="#f3e600" stroke-width="1.5"/></svg>
      <div class="step step-2">
        <span class="step-number">2</span>
        <span class="step-text">Speak with<br>Distributor Rep.</span>
      </div>
      <svg class="step-arrow" style="left:336px; top:362px;" width="56" height="12" viewBox="0 0 56 12"><line x1="0" y1="7" x2="50" y2="5" stroke="#f3e600" stroke-width="1.5"/><path d="M46 1 L54 5 L46 9" fill="none" stroke="#f3e600" stroke-width="1.5"/></svg>
      <div class="step step-3">
        <span class="step-number">3</span>
        <span class="step-text">Beginning training</span>
      </div>
    </section>
  </div>
</body>
</html>
```